Wealth Education Business Needs Sharp Business Card Design

We need a business card design for a recently launched investor education business called Harbor Crest.

The final design should promote security, empowerment, self improvement and financial gain. The card will ideally promote the stature of the business.

For more information and colours please visit harborcrest.com.au

Target Market(s)

Corporate executives and high net worth individuals

Industry/Entity Type

Education

Contact Information for Business Card

```html
<!DOCTYPE html>
<html lang="en">
<head>
<meta charset="utf-8">
<title>Harbor Crest — Business Card</title>
<link rel="stylesheet" href="https://fonts.googleapis.com/css2?family=Michroma&display=swap">
<style>
  :root {
    --page: #e9eaeb;
    --card-light: #ffffff;
    --card-shade: #eeeeee;
    --ink: #2f2f31;
    --ink-soft: #4a4a4d;
    --teal: #0f6e6c;
    --charcoal: #47474a;
    --rule: #8c8c8f;
    --brand: #1f8fa8;
  }
  * { margin: 0; padding: 0; box-sizing: border-box; }
  html, body { width: 1200px; height: 900px; overflow: hidden; background: var(--page); }
  body {
    font-family: "Michroma", sans-serif;
    color: var(--ink);
    display: flex;
    flex-direction: column;
    align-items: center;
    justify-content: center;
    gap: 40px;
  }
  .card {
    position: relative;
    width: 700px;
    height: 400px;
    border-radius: 34px;
    overflow: hidden;
    background: radial-gradient(ellipse at 60% 35%, var(--card-light) 0%, var(--card-shade) 100%);
    box-shadow: 0 6px 18px rgba(0,0,0,0.12);
  }
  .corner-art {
    position: absolute;
    left: 0;
    bottom: 0;
    width: 130px;
    height: 260px;
    background: linear-gradient(160deg, var(--teal) 0%, var(--charcoal) 100%);
  }
  .brand {
    position: absolute;
    display: flex;
    align-items: center;
    gap: 14px;
    color: var(--brand);
    letter-spacing: 0.14em;
    white-space: nowrap;
  }
  .brand-dot { border-radius: 50%; background: var(--brand); flex: none; }
  .front .brand { left: 300px; top: 86px; font-size: 24px; }
  .front .brand-dot { width: 34px; height: 34px; }
  .back .brand { left: 50%; top: 50%; transform: translate(-50%, -50%); font-size: 34px; gap: 20px; }
  .back .brand-dot { width: 48px; height: 48px; }

  .details {
    position: absolute;
    left: 170px;
    top: 170px;
    display: flex;
    gap: 18px;
  }
  .identity {
    text-align: right;
    width: 240px;
    font-size: 11px;
    line-height: 1.7;
    color: var(--ink-soft);
    letter-spacing: 0.06em;
    white-space: nowrap;
  }
  .identity .person { font-size: 14px; color: var(--ink); letter-spacing: 0.1em; }
  .identity .role { margin-bottom: 4px; }
  .divider { width: 1px; background: var(--rule); height: 110px; }
  .contacts { list-style: none; font-size: 12px; letter-spacing: 0.08em; color: var(--ink); white-space: nowrap; }
  .contacts li { display: flex; align-items: center; gap: 8px; height: 21px; }
  .contacts svg { width: 13px; height: 13px; flex: none; }
</style>
</head>
<body>

  <section class="card front" aria-label="Business card front">
    <div class="corner-art" role="img" aria-label="Decorative corner artwork in teal and charcoal tones"></div>

    <div class="brand"><span class="brand-dot"></span><span class="brand-name">HARBOR CREST</span></div>

    <div class="details">
      <div class="identity">
        <p class="person">Daniel Reeve</p>
        <p class="role">Owner / C.E.O</p>
        <p class="address">Level 4, 18 Quay St,</p>
        <p class="address">NSW 2000</p>
      </div>
      <div class="divider"></div>
      <ul class="contacts">
        <li><svg viewBox="0 0 14 14"><circle cx="7" cy="7" r="7" fill="var(--ink)"/><path d="M4.5 4 L6 3.6 L6.6 5.4 L5.7 6 Q6.3 7.6 8 8.3 L8.6 7.4 L10.4 8 L10 9.5 Q6.5 10 4.5 4 Z" fill="#fff"/></svg>555-210-4418</li>
        <li><svg viewBox="0 0 14 14"><circle cx="7" cy="7" r="7" fill="var(--ink)"/><rect x="5" y="3" width="4" height="8" rx="0.8" fill="#fff"/></svg>555-382-9061</li>
        <li><svg viewBox="0 0 14 14"><circle cx="7" cy="7" r="7" fill="var(--ink)"/><rect x="3.5" y="6" width="7" height="4" fill="#fff"/><rect x="5" y="3.5" width="4" height="2.5" fill="#fff"/></svg>555-647-2035</li>
        <li><svg viewBox="0 0 14 14"><circle cx="7" cy="7" r="7" fill="var(--ink)"/><rect x="3.5" y="4.5" width="7" height="5" fill="#fff"/><path d="M3.5 4.5 L7 7.5 L10.5 4.5" stroke="var(--ink)" stroke-width="0.8" fill="none"/></svg>info@harborcrest.com.au</li>
        <li><svg viewBox="0 0 14 14"><circle cx="7" cy="7" r="7" fill="var(--ink)"/><circle cx="7" cy="7" r="3.6" stroke="#fff" stroke-width="0.9" fill="none"/><path d="M3.4 7 H10.6 M7 3.4 V10.6" stroke="#fff" stroke-width="0.8"/></svg>www.harborcrest.com.au</li>
      </ul>
    </div>
  </section>

  <section class="card back" aria-label="Business card back">
    <div class="brand"><span class="brand-dot"></span><span class="brand-name">HARBOR CREST</span></div>
  </section>

</body>
</html>
```